Lorvex Tilo medical cannibis cultivation company

tag - Tilo rise
Lorvex Tilo medical cannabis cultivation - logo is selected- can we please see bold examples with our selection. We are mainly dealing with medical companies and professionals. We would like to be stand out in the crowd with our designs. Welcome any and all attempts. Thanks

Target Market(s)

Medical and Professional

Industry/Entity Type

Medical And Science

Font styles to use
Sans Serif

Colors

Designer to choose colors to be used in the design.

Requirements
Must have
• Bright colour and be bold- Love the teal and magenta that is currently on the dark background design.
Nice to have
• shading and the 3D affect- The shadowed appearance.
Should not have
• Anything related to illegal activity or un professional manners

```html
<!DOCTYPE html>
<html lang="en">
<head>
<meta charset="utf-8">
<title>Lorvex Tilo – Business Card</title>
<link href="https://fonts.googleapis.com/css2?family=Roboto:wght@400;500;700&display=swap" rel="stylesheet">
<style>
  :root {
    --page: #d9d9d9;
    --ink: #000000;
    --teal: #00aee8;
    --magenta: #9e4c98;
    --steel: #8a9096;
    --ring: #9aa0a6;
    --white: #ffffff;
    --text-dark: #0b1a26;
  }
  * { box-sizing: border-box; margin: 0; padding: 0; }
  html, body { width: 1125px; height: 1200px; overflow: hidden; }
  body {
    background: var(--page);
    font-family: "Roboto", Arial, sans-serif;
    position: relative;
  }
  .card {
    position: absolute;
    left: 150px;
    width: 825px;
    height: 471px;
    border-radius: 24px;
    overflow: hidden;
    box-shadow: 0 14px 28px rgba(0,0,0,0.28);
  }
  .card--front { top: 98px; background: var(--ink); }
  .card--back { top: 631px; background: var(--magenta); }

  .wave { position: absolute; inset: 0; width: 100%; height: 100%; }

  .brand-ring {
    position: absolute;
    left: 122px; top: 52px;
    width: 150px; height: 150px;
    border-radius: 50%;
    border: 5px solid var(--ring);
  }
  .brand-name {
    position: absolute;
    left: 40px; width: 314px; top: 210px;
    text-align: center;
    font-size: 38px;
    line-height: 44px;
    font-weight: 500;
    letter-spacing: 1px;
    color: var(--teal);
    white-space: nowrap;
  }
  .brand-tag {
    position: absolute;
    left: 40px; width: 314px; top: 258px;
    text-align: center;
    font-size: 17px;
    line-height: 20px;
    letter-spacing: 3px;
    color: #c8ccd0;
    text-transform: uppercase;
  }

  .contact {
    position: absolute;
    right: 50px; top: 222px;
    text-align: right;
    color: var(--text-dark);
  }
  .contact__name {
    font-size: 28px; line-height: 32px; font-weight: 700; letter-spacing: 0.5px;
    text-shadow: 0 1px 2px rgba(0,0,0,0.25);
  }
  .contact__role { font-size: 19px; line-height: 24px; font-weight: 500; margin-top: 1px; }
  .contact__address { font-size: 18px; line-height: 25px; margin-top: 20px; }
  .contact__lines { margin-top: 12px; font-size: 18px; line-height: 26px; }
  .contact__line { display: flex; justify-content: flex-end; align-items: center; gap: 8px; }
  .contact__line svg { width: 16px; height: 16px; fill: var(--text-dark); }

  .back-ring {
    position: absolute;
    left: 282px; top: 100px;
    width: 260px; height: 260px;
    border-radius: 50%;
    border: 6px solid var(--white);
  }
  .back-name {
    position: absolute;
    left: 0; right: 0; top: 212px;
    text-align: center;
    font-size: 28px; line-height: 36px; font-weight: 500; letter-spacing: 1px;
    color: var(--white);
    white-space: nowrap;
  }
  .back-url {
    position: absolute;
    left: 0; right: 0; top: 406px;
    text-align: center;
    font-size: 18px; letter-spacing: 5px;
    color: var(--white);
  }
</style>
</head>
<body>

<section class="card card--front">
  <svg class="wave" viewBox="0 0 800 456" preserveAspectRatio="none" aria-hidden="true">
    <path fill="var(--magenta)" d="M30,372 C180,402 280,372 400,300 S620,150 760,145 C780,145 800,148 800,150 L800,456 L0,456 L0,372 Z"/>
    <path fill="var(--steel)" d="M0,362 C150,412 270,392 400,314 S630,158 800,152 L800,456 L0,456 Z"/>
    <path fill="var(--ink)" d="M0,395 C150,432 270,410 400,330 S640,162 800,155 L800,456 L0,456 Z"/>
    <path fill="var(--teal)" d="M0,400 C150,438 270,416 400,336 S645,168 800,158 L800,456 L0,456 Z"/>
  </svg>

  <div class="brand-ring"></div>
  <div class="brand-name">LORVEX TILO</div>
  <div class="brand-tag">Tilo rise</div>

  <div class="contact">
    <div class="contact__name">MARA DEVLIN</div>
    <div class="contact__role">CEO/FOUNDER</div>
    <div class="contact__address">412 Larkfield Road<br>Northvale, Alaska 99871</div>
    <div class="contact__lines">
      <div class="contact__line">555 014 2938
        <svg viewBox="0 0 24 24"><path d="M6.6 10.8a15.1 15.1 0 0 0 6.6 6.6l2.2-2.2a1 1 0 0 1 1-.25 11.4 11.4 0 0 0 3.6.57 1 1 0 0 1 1 1V20a1 1 0 0 1-1 1A17 17 0 0 1 3 4a1 1 0 0 1 1-1h3.5a1 1 0 0 1 1 1c0 1.25.2 2.45.57 3.57a1 1 0 0 1-.25 1z"/></svg>
      </div>
      <div class="contact__line">mara@lorvextilo.com
        <svg viewBox="0 0 24 24"><path d="M2 5h20v14H2z M4 7v.5l8 5 8-5V7l-8 5z" fill-rule="evenodd"/></svg>
      </div>
      <div class="contact__line">www.lorvextilo.com
        <svg viewBox="0 0 24 24"><circle cx="12" cy="12" r="10"/><path d="M2 12h20M12 2c3 3 3 17 0 20M12 2c-3 3-3 17 0 20" stroke="#00aee8" stroke-width="1.6" fill="none"/></svg>
      </div>
    </div>
  </div>
</section>

<section class="card card--back">
  <div class="back-ring"></div>
  <div class="back-name">LORVEX TILO</div>
  <div class="back-url">www.lorvextilorise.com</div>
</section>

</body>
</html>
```